we can communicate on this, but i want to follow the approach we took on Pellew|Marsh & Quinlan but i feel the card front needs the black background and the platinum and gold logo. The back? I am open. we can use the same info from PM&Q. Velmont Arc is an enhanced equity investment fund - basically a very exclusive boutique hedge fund that uses only stock options. very advanced things. hope you are interested

Contact Information for Business Card

Dr. Lewis T. Brennick, CFA
Scientifique de fusée financière
701.555.0143
LTBquant47@mailvantor.com

4718 Willow Creek Bend W.
West Fargo, ND 58078

No web site

Colors

Designer to choose colors to be used in the design.

Requirements
Nice to have
• I tend to prefer the most visible applications of the logo to include logo and name, the logo version with a black background and the gold and platinum components separated by the black. I see this working well for a single side (logo and name - this is card front to me).
• I am fairly open to other treatments on the reverse side with the data. To me, it makes sense to have a different color rendition of the logo on the reverse and it may be a muted black tone on tone or an oversized portion that would have spot UV. Or, the reverse may play with colors and layout
Should not have
• Other colors = no no
• Decorative font

```html
<!DOCTYPE html>
<html lang="fr">
<head>
<meta charset="utf-8">
<title>Velmont Arc — Business Card</title>
<link href="https://fonts.googleapis.com/css2?family=Cinzel:wght@400;600&display=swap" rel="stylesheet">
<style>
  :root {
    --backdrop: #2a2a2c;
    --card-black: #111113;
    --card-white: #ffffff;
    --ink: #1e1f21;
    --ink-soft: #3a3b3e;
    --gold: #c9a23c;
    --platinum: #c9ccd1;
  }
  * { box-sizing: border-box; margin: 0; padding: 0; }
  html, body {
    width: 1200px; height: 900px; overflow: hidden;
    background: var(--backdrop);
    font-family: "Cinzel", serif;
  }
  .stage {
    width: 1200px; height: 900px;
    display: flex; flex-direction: column; align-items: center; justify-content: center;
    gap: 40px;
  }
  .card {
    position: relative;
    width: 640px; height: 366px;
    border-radius: 22px;
    overflow: hidden;
  }

  /* Logo side */
  .card--brand {
    background: var(--card-black);
    display: flex; align-items: center; justify-content: center;
  }
  .brand-mark {
    display: flex; flex-direction: column; align-items: center; gap: 18px;
  }
  .brand-mark__dot {
    width: 92px; height: 92px; border-radius: 50%;
    background: var(--gold);
  }
  .brand-mark__name {
    font-weight: 600; font-size: 38px; letter-spacing: 3px;
    color: var(--platinum);
    white-space: nowrap;
  }

  /* Data side */
  .card--details { background: var(--card-white); }
  .accent-bar {
    position: absolute; left: 28px; top: 50px;
    width: 12px; height: 50px; background: var(--gold);
  }
  .identity { position: absolute; left: 56px; top: 48px; }
  .identity__name {
    font-weight: 600; font-size: 23px; color: var(--gold); letter-spacing: 0.5px;
    white-space: nowrap;
  }
  .identity__credential {
    font-size: 15px; color: var(--ink-soft); margin-top: 2px;
  }
  .identity__title {
    font-size: 15px; color: var(--ink-soft); margin-top: 12px; letter-spacing: 0.5px;
    white-space: nowrap;
  }
  .contact { position: absolute; left: 56px; top: 170px; list-style: none; }
  .contact__item {
    display: flex; align-items: center; gap: 10px;
    font-size: 14px; color: var(--ink-soft); margin-bottom: 8px;
    white-space: nowrap;
  }
  .contact__icon { width: 15px; height: 15px; flex: none; }

  .logo-lockup {
    position: absolute; right: 40px; top: 70px;
    display: flex; flex-direction: column; align-items: center; gap: 12px;
  }
  .logo-lockup__dot {
    width: 80px; height: 80px; border-radius: 50%; background: var(--gold);
  }
  .logo-lockup__name {
    font-weight: 600; font-size: 22px; letter-spacing: 2px; color: var(--ink);
    white-space: nowrap;
  }

  .address-band {
    position: absolute; left: 0; top: 262px;
    width: 590px; height: 42px;
    background: var(--ink);
    display: flex; align-items: center;
    padding-left: 40px;
    font-size: 14px; letter-spacing: 0.5px; color: var(--card-white);
    white-space: nowrap;
  }
  .address-band__dot {
    position: absolute; right: 26px; top: 252px;
    width: 62px; height: 62px; border-radius: 50%;
    background: var(--gold);
    border: 4px solid var(--card-white);
  }
</style>
</head>
<body>
  <main class="stage">
    <section class="card card--brand" aria-label="Card front">
      <div class="brand-mark">
        <span class="brand-mark__dot"></span>
        <span class="brand-mark__name">VELMONT ARC</span>
      </div>
    </section>

    <section class="card card--details" aria-label="Card back">
      <span class="accent-bar"></span>
      <div class="identity">
        <h1 class="identity__name">DR. LEWIS T. BRENNICK</h1>
        <p class="identity__credential">CFA</p>
        <p class="identity__title">SCIENTIFIQUE DE FUSÉE FINANCIÈRE</p>
      </div>
      <ul class="contact">
        <li class="contact__item">
          <svg class="contact__icon" viewBox="0 0 24 24" aria-hidden="true">
            <path fill="#c9a23c" d="M6.6 10.8a15.1 15.1 0 0 0 6.6 6.6l2.2-2.2a1 1 0 0 1 1-.25 11.4 11.4 0 0 0 3.6.57 1 1 0 0 1 1 1V20a1 1 0 0 1-1 1A17 17 0 0 1 3 4a1 1 0 0 1 1-1h3.5a1 1 0 0 1 1 1c0 1.25.2 2.45.57 3.57a1 1 0 0 1-.25 1z"/>
          </svg>
          701.555.0143
        </li>
        <li class="contact__item">
          <svg class="contact__icon" viewBox="0 0 24 24" aria-hidden="true">
            <rect x="2" y="5" width="20" height="14" rx="2" fill="#c9a23c"/>
            <path d="M3 6l9 7 9-7" fill="none" stroke="#fff" stroke-width="1.8"/>
          </svg>
          LTBQUANT47@MAILVANTOR.COM
        </li>
      </ul>

      <div class="logo-lockup">
        <span class="logo-lockup__dot"></span>
        <span class="logo-lockup__name">VELMONT ARC</span>
      </div>

      <div class="address-band">4718 WILLOW CREEK BEND W. WEST FARGO, ND 58078</div>
      <span class="address-band__dot"></span>
    </section>
  </main>
</body>
</html>
```